Business Card Re-Design/Update

We'd like to update out business cards. I've included our current "Style guide" which has the colour scheme of the organisation in it. I've also included the branding files with logos etc in them.

I've also included a copy of one of our existing cards so that you can see how ugly/dated they look. I'd like a fresh modern corporate look.

Target Market(s)

These are for our clients, potential clients, industry contacts - like all business cards

Contact Information for Business Card

Name
Position
Company Address - Level 1, 47 Fernby Street, Carlow Qld 4072
Direct Phone
mobile
Email
Website -www.korvalit.com.au
Logo

Colors

Designer to choose colors to be used in the design.

Requirements
Must have
• Main Logo
• Cards will need to be editable to be able to personalize them for each new employee.
Nice to have
• The MapOut, ShipWell, KeepSteady would be okay to have if they can be sensibly and professionally added to the look without detracting from the main imagery.
• Maybe they could go on the back of the card? will leave this to your creative discretion as to whether/where they fit.
Should not have
• Should not have decorative or script fonts

```html
<!DOCTYPE html>
<html lang="en">
<head>
<meta charset="utf-8">
<title>korvalIT business card</title>
<link rel="stylesheet" href="https://fonts.googleapis.com/css2?family=Roboto:wght@400;500;700&display=swap">
<style>
  :root {
    --backdrop: #8f8f8f;
    --card-white: #f1f1f2;
    --brand-red: #b3161d;
    --brand-red-dark: #8c0b11;
    --ink: #2b2b2b;
    --ink-soft: #555557;
    --rule: #3a3a3a;
    --tagline: #ececec;
  }
  html, body {
    margin: 0;
    padding: 0;
    width: 1105px;
    height: 1200px;
    overflow: hidden;
    background: var(--backdrop);
    font-family: "Roboto", Arial, sans-serif;
  }
  .canvas {
    position: relative;
    width: 1105px;
    height: 1200px;
  }
  .card {
    position: absolute;
    left: 182px;
    width: 746px;
    height: 427px;
    overflow: hidden;
  }
  .card-front {
    top: 119px;
    background: var(--card-white);
  }
  .card-back {
    top: 637px;
    height: 425px;
    background: linear-gradient(180deg, var(--brand-red) 0%, var(--brand-red-dark) 100%);
  }

  /* Front: company name */
  .company {
    position: absolute;
    top: 54px;
    left: 432px;
    display: flex;
    align-items: center;
    gap: 14px;
  }
  .company-square {
    width: 34px;
    height: 34px;
    background: var(--brand-red);
  }
  .company-name {
    font-size: 38px;
    font-weight: 500;
    color: var(--ink);
    letter-spacing: -0.5px;
  }

  /* Front: person */
  .person {
    position: absolute;
    top: 114px;
    left: 0;
  }
  .person-name {
    margin: 0 0 0 43px;
    font-size: 23px;
    font-weight: 500;
    color: var(--brand-red);
    letter-spacing: 0.3px;
    text-transform: uppercase;
  }
  .person-title {
    margin: 2px 0 0 43px;
    font-size: 17px;
    font-weight: 500;
    color: var(--ink);
  }
  .person-rule {
    width: 296px;
    height: 0;
    border-top: 1.5px solid var(--rule);
    margin-top: 8px;
  }

  .address {
    position: absolute;
    top: 188px;
    left: 43px;
    margin: 0;
    font-size: 18px;
    line-height: 22px;
    color: var(--ink-soft);
    font-style: normal;
  }

  .contacts {
    position: absolute;
    top: 245px;
    left: 43px;
    margin: 0;
    padding: 0;
    list-style: none;
  }
  .contacts li {
    display: flex;
    align-items: center;
    height: 23.6px;
    font-size: 18px;
    color: var(--ink-soft);
  }
  .contacts svg {
    width: 15px;
    height: 15px;
    margin-right: 14px;
    fill: var(--brand-red);
    flex: none;
  }

  /* Back: service taglines */
  .taglines {
    position: absolute;
    right: 44px;
    top: 192px;
    margin: 0;
    padding: 0;
    list-style: none;
    text-align: right;
  }
  .taglines li {
    font-size: 55px;
    line-height: 66px;
    font-weight: 500;
    color: var(--tagline);
    letter-spacing: -0.5px;
  }
</style>
</head>
<body>
<main class="canvas">

  <section class="card card-front" aria-label="Card front">
    <div class="company">
      <span class="company-square"></span>
      <span class="company-name">korvalIT</span>
    </div>

    <div class="person">
      <h1 class="person-name">Dana Whitfield</h1>
      <p class="person-title">Business Development Manager</p>
      <div class="person-rule"></div>
    </div>

    <address class="address">
      Level 1, 47 Fernby Street<br>
      Carlow Qld 4072
    </address>

    <ul class="contacts">
      <li>
        <svg viewBox="0 0 16 16" aria-hidden="true"><path d="M3.2 1l2.6 3-1.4 1.8c.9 2 2.6 3.7 4.8 4.8L11 9.2l3 2.6-1.6 2.7C7 14.5 1.5 9 1.5 3.6z"/></svg>
        +61 (0)7 5550 1820
      </li>
      <li>
        <svg viewBox="0 0 16 16" aria-hidden="true"><path d="M3.2 1l2.6 3-1.4 1.8c.9 2 2.6 3.7 4.8 4.8L11 9.2l3 2.6-1.6 2.7C7 14.5 1.5 9 1.5 3.6z"/></svg>
        +61 (0)7 5550 1836
      </li>
      <li>
        <svg viewBox="0 0 16 16" aria-hidden="true"><path d="M4.5 0h7A1.5 1.5 0 0113 1.5v13a1.5 1.5 0 01-1.5 1.5h-7A1.5 1.5 0 013 14.5v-13A1.5 1.5 0 014.5 0zM5 2v10h6V2zm3 11a1 1 0 100 2 1 1 0 000-2z"/></svg>
        +61 (0)400 555 274
      </li>
      <li>
        <svg viewBox="0 0 16 16" aria-hidden="true"><path d="M4 1h8v4H4zM1 6h14v7h-2v-2H3v2H1zm3 6h8v3H4z"/></svg>
        +61 (0)7 5550 1809
      </li>
      <li>
        <svg viewBox="0 0 16 16" aria-hidden="true"><path d="M1 3h14v1.2L8 9 1 4.2zm0 2.6l7 4.8 7-4.8V13H1z"/></svg>
        dwhitfield@korvalit.com.au
      </li>
      <li>
        <svg viewBox="0 0 16 16" aria-hidden="true"><path d="M8 1a7 7 0 100 14A7 7 0 008 1zm0 1.6c.9 0 1.9 1.6 2.3 4.1H5.7C6.1 4.2 7.1 2.6 8 2.6zM2.7 7.6h2.9c0 .3 0 .6 0 .9s0 .6 0 .9H2.7zm7.8 0h2.8v1.8h-2.8zm-4.8 2.8h4.6c-.4 2.4-1.4 3-2.3 3s-1.9-.6-2.3-3z"/></svg>
        www.korvalit.com.au
      </li>
    </ul>
  </section>

  <section class="card card-back" aria-label="Card back">
    <ul class="taglines">
      <li>MapOut</li>
      <li>ShipWell</li>
      <li>KeepSteady</li>
    </ul>
  </section>

</main>
</body>
</html>
```